Calder Vane LED - E- Commerce site

We need a website designed for an LED Billboard company that sells:
1) LED Billboards (Sales & Rental)
2) LED Gas Station lights
3) Truss Systems (Sales & Rental)
4) Sound Systems (Sales & Rental)

Attached are websites that sell similar products as Calder Vane LED. Target market is for business, property managers and event coordinators.
This site will need to be an e-commerce site where customers can purchase the product directly from the site. What I'm looking for is a design layout to start.

Conceptual Web Designs:
http://192.0.2.47:8087/index.html
http://www.pmvdisplay.example/
http://www.auralomaaudio.example/
http://www.quillmarkpanel.example/

Attached is the logo of the company: Please note that the new spelling of the logo is "Calder Vane LED" using domain " CalderVaneLED.com

Industry/Entity Type

Gas Station

Number of Pages Required

5+ page

Requirements
Must have
• 1) E-Commerce - Customers will need to be able to order product from the site.
• 2) Customers will also have the option to rent the product as well.
Nice to have
• I like the image of the attached website, that has a video clip loop
• http://www.quillmarkpanel.example/

```html
<!DOCTYPE html>
<html lang="en">
<head>
<meta charset="utf-8">
<title>Calder Vane LED</title>
<link rel="stylesheet" href="https://fonts.googleapis.com/css2?family=Open+Sans:wght@400;600;700&family=Oswald:wght@400;500&display=swap">
<style>
:root{
  --dark:#161616;
  --darker:#111111;
  --red:#e3262b;
  --yellow:#fcc011;
  --text:#333333;
  --muted:#8a8a8a;
  --light:#ebebeb;
  --line:#dcdcdc;
  --link:#2a7ad6;
}
*{box-sizing:border-box;margin:0;padding:0}
html,body{width:1200px;height:2214px;overflow:hidden}
body{font-family:'Open Sans',sans-serif;color:var(--text);background:#fff;font-size:13px}
.wrap{width:938px;margin:0 auto;position:relative}
a{color:inherit;text-decoration:none}

/* header */
.site-header{background:var(--dark);height:136px}
.site-header .wrap{height:136px}
.top-links{position:absolute;right:0;top:13px;font-size:11.5px;color:#a9a9a9;letter-spacing:.2px}
.top-links > span{margin-left:12px}
.top-links .sep{color:#666}
.top-links .phone{color:var(--red)}
.brand{position:absolute;left:0;top:28px;display:flex;align-items:center;gap:12px}
.brand-mark{width:56px;height:56px;border-radius:50%;background:var(--red)}
.brand-name{font-weight:700;font-size:24px;color:var(--yellow)}
.search{position:absolute;left:411px;top:61px;width:333px;height:42px;border:1px solid #3a3a3a;display:flex;align-items:center;padding-left:16px;font-style:italic;font-size:12px;color:#5b5b5b}
.search svg{position:absolute;right:14px;top:13px}
.cart{position:absolute;right:0;top:61px;width:167px;height:42px;border:1px solid #3a3a3a;display:flex;align-items:center;padding-left:14px;gap:10px;font-size:12px;color:#ddd}

/* nav */
.main-nav{background:var(--red);height:47px}
.main-nav ul{list-style:none;display:flex;height:47px;align-items:center}
.main-nav li{color:#fff;font-size:13px;font-weight:600;padding:0 19px;height:47px;display:flex;align-items:center;text-transform:uppercase}
.main-nav li.active{background:var(--yellow);color:#222}
.main-nav li:nth-child(2){padding-right:10px}

/* hero */
.hero{height:395px;background:linear-gradient(90deg,#3a2a2a,#5c5555 40%,#4a3a3f 70%,#2b2b33);position:relative}
.hero-slide{position:absolute;left:0;top:30px;width:635px;height:333px;background:#fff}
.hero-photo{position:absolute;left:0;top:0;width:635px;height:333px;background:linear-gradient(180deg,#f6f6f6,#dcdcdc)}
.hero-title{position:absolute;left:20px;top:192px;font-family:'Oswald',sans-serif;font-weight:400;font-size:31px;line-height:36px;color:#222;text-transform:uppercase;letter-spacing:-.3px}
.hero-title em{font-style:normal;color:var(--red)}
.btn{display:inline-flex;align-items:center;justify-content:center;font-size:11.5px;font-weight:700;text-transform:uppercase}
.btn-yellow{background:var(--yellow);color:#222}
.btn-red{background:var(--red);color:#fff}
.hero-cta{position:absolute;left:20px;top:283px;width:103px;height:30px}
.hero-arrows{position:absolute;right:23px;top:283px;display:flex;gap:2px}
.hero-arrows span{width:31px;height:30px;background:var(--yellow);display:flex;align-items:center;justify-content:center}
.promo{position:absolute;left:651px;width:287px;height:158px;overflow:hidden}
.promo-sound{top:30px;background:linear-gradient(120deg,#0c0c0c 40%,#2a3540)}
.promo-truss{top:205px;background:linear-gradient(120deg,#b02a9c,#d94cc4 60%,#7a1c6c)}
.promo h3{position:absolute;left:14px;top:6px;font-family:'Oswald',sans-serif;font-weight:400;font-size:36px;letter-spacing:1px;line-height:40px}
.promo-sound h3{color:#ee2a7b}
.promo-truss h3{color:#fff}
.promo h4{position:absolute;left:14px;top:48px;font-size:15px;font-weight:600;color:#fff}
.promo p{position:absolute;left:14px;top:72px;font-size:11px;color:#ddd;text-transform:uppercase}
.promo .off{position:absolute;font-family:'Oswald',sans-serif;font-weight:400;font-size:28px;color:#fff}
.promo .off b{font-weight:400;color:#3ab0f0}
.promo .off sup{font-size:13px}
.promo-sound .btn{position:absolute;left:15px;top:116px;width:89px;height:27px}
.promo-sound .off{right:20px;top:110px}
.promo-truss .btn{position:absolute;right:15px;top:114px;width:89px;height:27px}
.promo-truss .off{left:16px;top:108px}

/* products */
.featured{padding-top:37px;height:810px}
.section-head{display:flex;justify-content:space-between;align-items:center;height:30px}
.section-title{font-size:17px;font-weight:600;letter-spacing:.6px;text-transform:uppercase;color:#222}
.filters{display:flex;gap:4px;font-size:11px;color:#777;text-transform:uppercase}
.filters span{padding:7px 10px}
.filters .on{background:#e2e2e2;color:#333}
.grid{display:grid;grid-template-columns:repeat(4,218px);gap:19px 22px;margin-top:20px}
.card{border:1px solid var(--line);height:337px;text-align:center}
.card-photo{height:189px;border-bottom:1px solid var(--line);background:radial-gradient(circle,#d8d8d8 0,#f4f4f4 45%,#fff 70%)}
.card h5{font-size:12.5px;font-weight:700;color:#222;margin-top:20px}
.card p{font-size:11.5px;color:var(--muted);line-height:18px;margin-top:7px;padding:0 20px}
.card-actions{display:flex;justify-content:center;gap:3px;margin-top:13px}
.card-actions .btn{width:91px;height:33px}

/* features */
.features{background:var(--light);height:156px}
.features .wrap{display:grid;grid-template-columns:repeat(4,1fr);padding-top:26px}
.feature h6{font-size:15px;font-weight:700;letter-spacing:.5px;color:#222;display:flex;align-items:center;gap:8px;text-transform:uppercase;height:22px;line-height:22px}
.feature h6 .pct{font-size:20px;line-height:22px}
.feature p{font-size:11.5px;line-height:18px;color:var(--muted);margin-top:7px;width:200px}
.feature a{color:var(--link);font-size:11.5px;line-height:18px}

/* about */
.about{height:270px}
.about .wrap{display:flex;padding-top:34px}
.about-text{width:450px}
.about-text p{font-size:12px;line-height:20px;color:#777;margin-top:22px}
.about-text p+p{margin-top:6px}
.certs{margin-left:64px;width:424px}
.cert-grid{display:grid;grid-template-columns:repeat(3,1fr);gap:22px 28px;margin-top:24px}
.cert{height:44px;border-radius:6px;background:#e4e4e4}

/* signup */
.signup{background:var(--light);height:87px}
.signup .wrap{display:flex;align-items:center;height:87px}
.signup label{font-size:14px;font-weight:700;letter-spacing:.4px;color:#222;text-transform:uppercase}
.email-box{margin-left:22px;width:254px;height:33px;background:#fff;font-style:italic;font-size:11.5px;color:#aaa;display:flex;align-items:center;padding-left:15px}
.signup .btn{width:99px;height:33px}
.divider{width:1px;height:40px;background:#c9c9c9;margin:0 38px 0 46px}
.social{display:flex;gap:12px;margin-left:22px}
.social span{width:33px;height:33px;background:#5a5a5a}

/* footer */
.site-footer{background:var(--darker);height:257px}
.site-footer .wrap{display:flex;padding-top:30px}
.col h6{color:var(--yellow);font-size:12.5px;font-weight:700;text-transform:uppercase;letter-spacing:.3px;margin-bottom:12px}
.col li{list-style:none;font-size:11.5px;color:#9a9a9a;line-height:24.5px}
.col-1{width:160px}.col-2{width:172px}.col-3{width:214px}.col-4{width:188px}
.contact-row{display:flex;gap:12px;font-size:11.5px;color:#9a9a9a;line-height:19px;margin-bottom:12px}
.contact-row svg{flex:none;margin-top:2px}
.bottom-bar{background:var(--darker);border-top:1px solid #262626;height:56px}
.bottom-bar .wrap{display:flex;justify-content:space-between;align-items:center;height:56px;font-size:11.5px;color:#9a9a9a}
.pay{display:flex;align-items:center;gap:10px}
.pay i{display:block;width:30px;height:20px;border-radius:3px;background:#4a4a4a}
</style>
</head>
<body>

<header class="site-header">
  <div class="wrap">
    <div class="brand"><span class="brand-mark"></span><span class="brand-name">Calder Vane LED</span></div>
    <div class="top-links">
      <span>CUSTOMER SERVICE: <em class="phone" style="font-style:normal">+123 456 7890</em></span>
      <span class="sep">|</span><span>MY ACCOUNT</span>
      <span class="sep">|</span><span>WISH LIST (0)</span>
      <span class="sep">|</span><span>CHECKOUT</span>
      <span class="sep">|</span><span>LOGIN</span>
    </div>
    <div class="search">SEARCH HERE...
      <svg width="15" height="15" viewBox="0 0 15 15"><circle cx="6" cy="6" r="4.6" fill="none" stroke="#e3262b" stroke-width="2"/><line x1="9.5" y1="9.5" x2="14" y2="14" stroke="#e3262b" stroke-width="2"/></svg>
    </div>
    <div class="cart">
      <svg width="24" height="20" viewBox="0 0 24 20"><path d="M1 2h4l3 11h12l3-8H7" fill="none" stroke="#fcc011" stroke-width="2"/><circle cx="9" cy="17" r="1.8" fill="#fcc011"/><circle cx="19" cy="17" r="1.8" fill="#fcc011"/></svg>
      <span>0 ITEM(S) - $0.00</span>
    </div>
  </div>
</header>

<nav class="main-nav">
  <div class="wrap">
    <ul>
      <li class="active">Home</li>
      <li>LED Lights Systems&nbsp;&nbsp;<svg width="8" height="5" viewBox="0 0 8 5"><path d="M0 0h8L4 5z" fill="#fff"/></svg></li>
      <li>Truss Systems</li>
      <li>Sound Systems</li>
      <li>Service and Support</li>
      <li>About</li>
      <li>Contact Us</li>
    </ul>
  </div>
</nav>

<section class="hero" role="img" aria-label="Blurred city street with illuminated billboards">
  <div class="wrap">
    <div class="hero-slide">
      <div class="hero-photo" role="img" aria-label="Row of LED bulbs and spotlights on a white shelf"></div>
      <h1 class="hero-title">More than<br>100 <em>LED</em> Products</h1>
      <a class="btn btn-yellow hero-cta">Click Here</a>
      <div class="hero-arrows">
        <span><svg width="8" height="12" viewBox="0 0 8 12"><path d="M7 1L2 6l5 5" fill="none" stroke="#fff" stroke-width="2"/></svg></span>
        <span><svg width="8" height="12" viewBox="0 0 8 12"><path d="M1 1l5 5-5 5" fill="none" stroke="#fff" stroke-width="2"/></svg></span>
      </div>
    </div>
    <div class="promo promo-sound" role="img" aria-label="Sound systems promotion with speaker">
      <h3>SOUND</h3><h4>SYSTEMS</h4><p>Simply dummy printing</p>
      <a class="btn btn-yellow">Buy Now!</a>
      <div class="off"><b>25<sup>%</sup></b>OFF</div>
    </div>
    <div class="promo promo-truss" role="img" aria-label="Truss systems promotion with stage lights">
      <h3>TRUSS</h3><h4>SYSTEMS</h4><p>Simply dummy printing</p>
      <div class="off"><b>25<sup>%</sup></b>OFF</div>
      <a class="btn btn-yellow">Buy Now!</a>
    </div>
  </div>
</section>

<section class="featured">
  <div class="wrap">
    <div class="section-head">
      <h2 class="section-title">Featured Products</h2>
      <div class="filters"><span class="on">All</span><span>LED Light</span><span>Gas Station Light</span><span>Truss Systems</span><span>Sound Systems</span></div>
    </div>
    <div class="grid">
      <article class="card"><div class="card-photo" role="img" aria-label="Recessed LED panel light"></div><h5>30W-LED Panel Light</h5><p>simply dummy text the printing and typesetting industry</p><div class="card-actions"><a class="btn btn-yellow">Buy Now</a><a class="btn btn-red">On Rent</a></div></article>
      <article class="card"><div class="card-photo" role="img" aria-label="LED tube light"></div><h5>20W-T8-LED Tube-UL</h5><p>simply dummy text the printing and typesetting industry</p><div class="card-actions"><a class="btn btn-yellow">Buy Now</a><a class="btn btn-red">On Rent</a></div></article>
      <article class="card"><div class="card-photo" role="img" aria-label="Portable USB sound system"></div><h5>Sistema Sonido Portatil USB</h5><p>simply dummy text the printing and typesetting industry</p><div class="card-actions"><a class="btn btn-yellow">Buy Now</a><a class="btn btn-red">On Rent</a></div></article>
      <article class="card"><div class="card-photo" role="img" aria-label="Stage light on truss arch"></div><h5>DJ Truss arch</h5><p>simply dummy text the printing and typesetting industry</p><div class="card-actions"><a class="btn btn-yellow">Buy Now</a><a class="btn btn-red">On Rent</a></div></article>
      <article class="card"><div class="card-photo" role="img" aria-label="DJ mixing deck controller"></div><h5>Korvel DJ Console 4</h5><p>simply dummy text the printing and typesetting industry</p><div class="card-actions"><a class="btn btn-yellow">Buy Now</a><a class="btn btn-red">On Rent</a></div></article>
      <article class="card"><div class="card-photo" role="img" aria-label="Square LED ceiling panel"></div><h5>30W-LED Panel Light</h5><p>simply dummy text the printing and typesetting industry</p><div class="card-actions"><a class="btn btn-yellow">Buy Now</a><a class="btn btn-red">On Rent</a></div></article>
      <article class="card"><div class="card-photo" role="img" aria-label="DJ table on truss stand"></div><h5>DJ Tables &amp; Stands</h5><p>simply dummy text the printing and typesetting industry</p><div class="card-actions"><a class="btn btn-yellow">Buy Now</a><a class="btn btn-red">On Rent</a></div></article>
      <article class="card"><div class="card-photo" role="img" aria-label="Pair of T5 LED tubes"></div><h5>Lumenra T5 LED</h5><p>simply dummy text the printing and typesetting industry</p><div class="card-actions"><a class="btn btn-yellow">Buy Now</a><a class="btn btn-red">On Rent</a></div></article>
    </div>
  </div>
</section>

<section class="features">
  <div class="wrap">
    <div class="feature"><h6><svg width="18" height="18" viewBox="0 0 18 18"><circle cx="9" cy="9" r="6.5" fill="none" stroke="#222" stroke-width="4" stroke-dasharray="3 2"/><circle cx="9" cy="9" r="4" fill="#222"/><circle cx="9" cy="9" r="2" fill="#ebebeb"/></svg>Technology</h6><p>t is long established fact the reader will be distracted by the readable content of a page...</p><a>Read More »</a></div>
    <div class="feature"><h6><span class="pct">%</span>Price</h6><p>t is long established fact the reader will be distracted by the readable content of a page...</p><a>Read More »</a></div>
    <div class="feature"><h6><svg width="18" height="18" viewBox="0 0 18 18"><rect x="1" y="3" width="13" height="13" fill="none" stroke="#222" stroke-width="2"/><path d="M4 9l4 4 9-11" fill="none" stroke="#222" stroke-width="2.5"/></svg>Quality</h6><p>t is long established fact the reader will be distracted by the readable content of a page...</p><a>Read More »</a></div>
    <div class="feature"><h6><svg width="18" height="18" viewBox="0 0 18 18"><circle cx="9" cy="9" r="7.5" fill="none" stroke="#222" stroke-width="1.8"/><path d="M9 4l1.5 3.3 3.5.3-2.7 2.3.9 3.5L9 11.5l-3.2 1.9.9-3.5L4 7.6l3.5-.3z" fill="#222"/></svg>Warranty</h6><p>t is long established fact the reader will be distracted by the readable content of a page...</p><a>Returns Policy »</a></div>
  </div>
</section>

<section class="about">
  <div class="wrap">
    <div class="about-text">
      <h2 class="section-title">About Calder Vane LED</h2>
      <p>It is a long established fact that a reader will be distracted by the readable content of a page when looking at its layout. The point of using Lorem Ipsum is that it has a more-or-less normal distribution of Content here, content here, making it look like readable English.</p>
      <p>Many desktop publishing packages and web page editors now use Lorem Ipsum as their default model text, and a search for 'lorem ipsum' will uncover many web sites still in their infancy...</p>
    </div>
    <div class="certs">
      <h2 class="section-title">Product Certification</h2>
      <div class="cert-grid">
        <div class="cert"></div><div class="cert"></div><div class="cert"></div>
        <div class="cert"></div><div class="cert"></div><div class="cert"></div>
      </div>
    </div>
  </div>
</section>

<section class="signup">
  <div class="wrap">
    <label>Sign up for deals:</label>
    <div class="email-box">Enter Your Email</div>
    <a class="btn btn-yellow">Sign Up</a>
    <span class="divider"></span>
    <label>Stay Connected:</label>
    <div class="social"><span></span><span></span><span></span><span></span></div>
  </div>
</section>

<footer class="site-footer">
  <div class="wrap">
    <div class="col col-1"><h6>Quick Links</h6><ul><li>Home</li><li>Products</li><li>Services</li><li>About Us</li><li>FAQ's</li></ul></div>
    <div class="col col-2"><h6>Need Help?</h6><ul><li>See All Help</li><li>Returns</li><li>Shipping</li><li>Warranty</li><li>Contact Us</li></ul></div>
    <div class="col col-3"><h6>Policies &amp; Info</h6><ul><li>Terms and Conditions</li><li>Policy for Sellers</li><li>Policy for Buyers</li><li>Shipping &amp; Refund Policies</li><li>Wholesale Policy</li><li>Privacy Policy</li></ul></div>
    <div class="col col-4"><h6>My Account</h6><ul><li>Sign in</li><li>Track Order</li></ul></div>
    <div class="col">
      <h6>Contact Us</h6>
      <div class="contact-row"><svg width="12" height="16" viewBox="0 0 12 16"><path d="M6 0a6 6 0 0 0-6 6c0 4.5 6 10 6 10s6-5.5 6-10a6 6 0 0 0-6-6z" fill="#8a8a8a"/><circle cx="6" cy="6" r="2.2" fill="#111"/></svg><span>Lorem Ipsum is simply dummy<br>Larchmont, AB T9Z 4K2</span></div>
      <div class="contact-row"><svg width="12" height="14" viewBox="0 0 12 14"><path d="M2 0l3 3-1.5 2a9 9 0 0 0 4 4L9 7.5l3 3-2 3C5 13 0 7 0 2z" fill="#8a8a8a"/></svg><span>Phone:<br>(123) 456 7890</span></div>
      <div class="contact-row"><svg width="13" height="10" viewBox="0 0 13 10"><rect width="13" height="10" fill="#8a8a8a"/><path d="M0 0l6.5 5L13 0" fill="none" stroke="#111" stroke-width="1.2"/></svg><span>Email:<br>info@caldervaneled.com</span></div>
    </div>
  </div>
</footer>
<div class="bottom-bar">
  <div class="wrap">
    <span>Copyright © 2016 - Calder Vane LED, All Rights Reserved</span>
    <div class="pay"><span>Accepted Payment :</span><i></i><i></i><i></i><i></i></div>
  </div>
</div>

</body>
</html>
```